New Boutique Pilates and Barre studio needs a flyer to promote classes.

Our studio is called 'The Willow Loft'. We are a boutique studio in Sydney that offers pilates mat and Barre classes with a maximum of 8 participants.

We need a flyer to promote our new studio that is opening mid-January 2015. Our goal is to motivate clients to cherish and nurture their bodies by participating in either our Pilates mat classes and/or our barre classes.

The flyer needs to communicate high-end, boutique classes that welcome those aged from 17-70 who would like achieve a stronger, leaner and dancer-like physique.

We would like our logo and a picture on the front with our contact details . The front should also say "First class is free!" (somewhere down the bottom).

A description of our classes as well as a map of our location should be on the back. Please see attached word document for copy.
I have attached our logo and contact details as well as pictures that may be used.

Please keep it uncluttered and elegant.
Updates

I have added a few pilates photos and a few requirements for the front of the flyer. Thanks

Industry/Entity Type

Boutique

Requirements
Must have

• MUST INCLUDE ON THE FRONT:
Please make sure my logo is very clear.

* Barre Classes
* Pilates Mat Classes
Private Studio in Castle Hill, Sydney
'First Class is free!'
Contact details: (Phone, website, email and address)

```html
<!DOCTYPE html>
<html lang="en">
<head>
<meta charset="utf-8">
<title>The Willow Loft – Flyer</title>
<link href="https://fonts.googleapis.com/css2?family=Maven+Pro:wght@400;500;600&display=swap" rel="stylesheet">
<style>
:root{
  --stage:#dcdcdc;
  --paper:#ffffff;
  --mist:#efefef;
  --blue:#3b9ad4;
  --pink:#e4559a;
  --charcoal:#3b3b3d;
  --ink:#4a4a4a;
  --soft-ink:#7a7a7a;
  --footer-ink:#e6e6e6;
}
*{box-sizing:border-box;margin:0;padding:0}
html,body{width:1200px;height:800px;overflow:hidden}
body{background:var(--stage);font-family:"Maven Pro",sans-serif;color:var(--ink);position:relative}
.sheet{position:absolute;top:32px;width:520px;height:736px;background:var(--paper);box-shadow:0 4px 18px rgba(0,0,0,.18);overflow:hidden}
.sheet--back{left:60px}
.sheet--front{left:620px}

/* shared footer */
.contact-bar{position:absolute;left:0;right:0;bottom:0;height:128px;background:var(--charcoal);color:var(--footer-ink);font-size:12px;line-height:1.45}
.contact{position:absolute;display:flex;align-items:flex-start;gap:12px}
.contact svg{flex:none;width:24px;height:24px;fill:var(--pink)}
.contact--phone{left:34px;top:26px}
.contact--address{left:34px;top:72px}
.contact--web{left:270px;top:26px}

/* back */
.intro{position:absolute;top:24px;left:30px;right:30px;height:226px;display:flex;gap:28px;overflow:hidden}
.intro__col{flex:1}
.intro h2{font-size:19px;font-weight:500;color:var(--blue);margin-bottom:8px}
.intro p{font-size:10px;line-height:1.45;color:var(--soft-ink)}
.intro p + p{margin-top:6px}
.capacity-band{position:absolute;top:262px;left:0;right:0;height:64px;background:var(--blue);color:#fff;text-align:center;font-size:17px;line-height:1.25;padding-top:11px}
.benefits{position:absolute;top:326px;left:0;right:0;height:282px;background:var(--mist)}
.benefits h3{position:absolute;top:14px;left:150px;font-size:14px;font-weight:500;color:var(--ink)}
.benefit-list{position:absolute;top:40px;list-style:none;font-size:11.5px;color:var(--ink)}
.benefit-list li{display:flex;align-items:center;gap:8px;height:21px}
.benefit-list--a{left:150px}
.benefit-list--b{left:330px}
.tick{width:13px;height:13px}
.map{position:absolute;left:0;right:0;top:110px;bottom:0;background:linear-gradient(160deg,#e3e0d9 0%,#d7d4cc 55%,#cfd9c4 100%)}

/* front */
.brand{position:absolute;top:26px;right:30px;display:flex;align-items:center;gap:8px;font-size:22px;font-weight:500;color:var(--charcoal)}
.brand__dot{width:12px;height:12px;border-radius:50%;background:var(--blue)}
.hero{position:absolute;top:72px;left:0;right:0;height:300px;background:linear-gradient(120deg,#cfe6ee 0%,#b9c9cf 40%,#3a3a3c 75%,#5b6a72 100%)}
.hero-band{position:absolute;top:372px;left:0;right:0;height:14px;background:var(--blue)}
.offer{position:absolute;top:296px;left:200px;width:150px;height:150px;border-radius:50%;background:var(--pink);border:4px solid #fff;box-shadow:0 0 0 2px var(--pink);display:flex;align-items:center;justify-content:center;text-align:center;color:#fff;font-size:22px;font-weight:500;line-height:1.1;text-transform:uppercase}
.pitch{position:absolute;top:478px;left:40px;right:40px;text-align:center;font-size:13px;line-height:1.5;color:var(--ink)}
</style>
</head>
<body>

<!-- Back of flyer -->
<section class="sheet sheet--back">
  <div class="intro">
    <div class="intro__col">
      <h2>Barre classes:</h2>
      <p>Our Barre classes are a 50 minute fusion of Pilates, dance and total body strengthening through the use of the ballet barre, light hand weights, pilates balls and body weight.</p>
      <p>We move to upbeat pop music, making it fun and easy to forget that you are working out! You do not need to be a dancer or have any dance experience to join in. If you love moving to music, this class is just right for you.</p>
    </div>
    <div class="intro__col">
      <h2>Pilates classes:</h2>
      <p>Our Pilates mat classes build deep core strength, improve posture and lengthen the body through controlled, mindful movement. Small groups mean every client receives personal guidance and gentle corrections throughout each session.</p>
    </div>
  </div>

  <div class="capacity-band">All of our classes have a maximum of 8 participants<br>so reserve your space!</div>

  <div class="benefits">
    <h3>Pilates offers benefits such as:</h3>
    <ul class="benefit-list benefit-list--a">
      <li><svg class="tick" viewBox="0 0 13 13"><rect x="0.75" y="0.75" width="11.5" height="11.5" fill="none" stroke="#e4559a" stroke-width="1.5"/><path d="M3 6.5l2.5 2.5L10 3.5" fill="none" stroke="#e4559a" stroke-width="1.8"/></svg>Core strength</li>
      <li><svg class="tick" viewBox="0 0 13 13"><rect x="0.75" y="0.75" width="11.5" height="11.5" fill="none" stroke="#e4559a" stroke-width="1.5"/><path d="M3 6.5l2.5 2.5L10 3.5" fill="none" stroke="#e4559a" stroke-width="1.8"/></svg>Body tone</li>
      <li><svg class="tick" viewBox="0 0 13 13"><rect x="0.75" y="0.75" width="11.5" height="11.5" fill="none" stroke="#e4559a" stroke-width="1.5"/><path d="M3 6.5l2.5 2.5L10 3.5" fill="none" stroke="#e4559a" stroke-width="1.8"/></svg>Flexibility</li>
    </ul>
    <ul class="benefit-list benefit-list--b">
      <li><svg class="tick" viewBox="0 0 13 13"><rect x="0.75" y="0.75" width="11.5" height="11.5" fill="none" stroke="#e4559a" stroke-width="1.5"/><path d="M3 6.5l2.5 2.5L10 3.5" fill="none" stroke="#e4559a" stroke-width="1.8"/></svg>Posture</li>
      <li><svg class="tick" viewBox="0 0 13 13"><rect x="0.75" y="0.75" width="11.5" height="11.5" fill="none" stroke="#e4559a" stroke-width="1.5"/><path d="M3 6.5l2.5 2.5L10 3.5" fill="none" stroke="#e4559a" stroke-width="1.8"/></svg>Balance</li>
      <li><svg class="tick" viewBox="0 0 13 13"><rect x="0.75" y="0.75" width="11.5" height="11.5" fill="none" stroke="#e4559a" stroke-width="1.5"/><path d="M3 6.5l2.5 2.5L10 3.5" fill="none" stroke="#e4559a" stroke-width="1.8"/></svg>Stamina</li>
    </ul>
    <div class="map" role="img" aria-label="Street map showing the studio location in Castle Hill"></div>
  </div>

  <footer class="contact-bar">
    <div class="contact contact--phone">
      <svg viewBox="0 0 24 24"><path d="M6.6 10.8a15.1 15.1 0 0 0 6.6 6.6l2.2-2.2a1 1 0 0 1 1-.25 11.4 11.4 0 0 0 3.6.57 1 1 0 0 1 1 1V20a1 1 0 0 1-1 1A17 17 0 0 1 3 4a1 1 0 0 1 1-1h3.5a1 1 0 0 1 1 1c0 1.250.2 2.45.57 3.57a1 1 0 0 1-.25 1z"/></svg>
      <div>Call Mara on:<br>0400 318 672</div>
    </div>
    <div class="contact contact--address">
      <svg viewBox="0 0 24 24"><path d="M12 2a7 7 0 0 0-7 7c0 5.2 7 13 7 13s7-7.8 7-13a7 7 0 0 0-7-7zm0 9.5A2.5 2.5 0 1 1 12 6.5a2.5 2.5 0 0 1 0 5z"/></svg>
      <div>24 Linden Grove<br>Castle Hill NSW 2154</div>
    </div>
    <div class="contact contact--web">
      <svg viewBox="0 0 24 24"><path d="M2 4h20v13H14v2h3v2H7v-2h3v-2H2zm2 2v9h16V6z"/></svg>
      <div>info@thewillowloft.com.au<br>www.thewillowloft.com.au</div>
    </div>
  </footer>
</section>

<!-- Front of flyer -->
<section class="sheet sheet--front">
  <div class="brand"><span class="brand__dot"></span>The Willow Loft</div>

  <div class="hero" role="img" aria-label="Photo of women stretching forward on mats with exercise balls in a bright Pilates studio"></div>
  <div class="hero-band"></div>

  <div class="offer">First<br>class is<br>free!</div>

  <p class="pitch">The Willow Loft is a boutique studio in Castle Hill, Sydney.<br>We offer Pilates mat and barre classes for adults of any age, who are seeking a stronger, leaner dancer-like physique.</p>

  <footer class="contact-bar">
    <div class="contact contact--phone">
      <svg viewBox="0 0 24 24"><path d="M6.6 10.8a15.1 15.1 0 0 0 6.6 6.6l2.2-2.2a1 1 0 0 1 1-.25 11.4 11.4 0 0 0 3.6.57 1 1 0 0 1 1 1V20a1 1 0 0 1-1 1A17 17 0 0 1 3 4a1 1 0 0 1 1-1h3.5a1 1 0 0 1 1 1c0 1.25.2 2.45.57 3.57a1 1 0 0 1-.25 1z"/></svg>
      <div>Call Mara on:<br>0400 318 672</div>
    </div>
    <div class="contact contact--address">
      <svg viewBox="0 0 24 24"><path d="M12 2a7 7 0 0 0-7 7c0 5.2 7 13 7 13s7-7.8 7-13a7 7 0 0 0-7-7zm0 9.5A2.5 2.5 0 1 1 12 6.5a2.5 2.5 0 0 1 0 5z"/></svg>
      <div>24 Linden Grove<br>Castle Hill NSW 2154</div>
    </div>
    <div class="contact contact--web">
      <svg viewBox="0 0 24 24"><path d="M2 4h20v13H14v2h3v2H7v-2h3v-2H2zm2 2v9h16V6z"/></svg>
      <div>info@thewillowloft.com.au<br>www.thewillowloft.com.au</div>
    </div>
  </footer>
</section>

</body>
</html>
```